Powerpoint Design for AI Consulting Company

Description
Velmora Quill Industries is a consulting and technology company that engineers AI transformations, automation, and decision intelligence for financial firms, mining companies, and supply chains.
We already have a logo and brand colors (see attached). We need a professional, modern PowerPoint template that reflects our brand identity and positioning.
Key Requirements
Use our logo and color palette (deep blue, orange, white/black backgrounds).
Clean, modern design with subtle technology-inspired elements (data flows, AI networks, abstract systems).
Must feel sophisticated, bold, and boardroom-ready for executive presentations.
Templates should support both dark and light backgrounds.
Deliverables
A reusable PowerPoint template (.PPTX) with at least these layouts:
Title / Cover slide – dramatic, logo placement, tagline space.
Agenda slide – clean, structured layout.
Section divider slides – strong use of brand colors.
Content slides – text + image, text + icon.
Charts & data slides – bar, line, pie, comparison table, infographics.
Case study / example project slide. - ROI / Transformation Journey
Timeline / roadmap slide.
Team profile slide.
Reframe Slide – A provocative insight that reframes the client’s current thinking.
Options & Trade-offs Slide – Matrix showing different paths and consequences.
Execution Roadmap Slide – Step-by-step phased implementation view.
Closing / thank-you slide with contact details.
Style Guide
Colors: Primary – deep blue (#0D3559), Secondary – orange (#E87722), Accents – silver/white.
Fonts: Modern sans-serif (e.g., Montserrat, Lato, or similar).
Visual elements: Abstract technology, data-inspired graphics, mathematical motifs. Avoid clutter or overly “sci-fi” looks.
Tone: Premium consulting + innovative AI firm.
Target Market(s)
Velmora Quill Industries’ target market is senior decision-makers in finance, mining, and supply chains, where complexity, risk, and ROI pressure are high. Primary buyers include family offices, boutique wealth managers, super funds, and mining/supply chain executives, who value insight-driven strategies, automation, and decision intelligence. A secondary market includes professional services (accounting, legal, medical) and regulated SMEs (daycare, aged care, community services) burdened by admin and compliance. The slide deck must appeal to a boardroom audience — authoritative, data-driven, and visually clean — while remaining flexible enough to adapt for SME professional services.
Look and feel
Each slider illustrates characteristics of the customer's brand and the style your logo design should communicate.

```html
<!DOCTYPE html>
<html lang="en">
<head>
<meta charset="utf-8">
<title>Velmora Quill Industries – Presentation Template</title>
<link href="https://fonts.googleapis.com/css2?family=Montserrat:wght@500;600;700;800&family=Lato:wght@400;700&display=swap" rel="stylesheet">
<style>
:root{
  --navy:#163a6e;
  --navy-deep:#0d2a52;
  --orange:#d65f1f;
  --text:#3a3f47;
  --muted:#5b6068;
  --rule:#d9dde3;
  --paper:#ffffff;
  --canvas:#ffffff;
  --blue-1:#6fb1e6;
  --blue-2:#0f5fb8;
  --blue-3:#0b3f7d;
  --blue-4:#1a7fcc;
  --blue-5:#0c2f5e;
  --blue-6:#1369c0;
}
*{margin:0;padding:0;box-sizing:border-box}
html,body{width:1050px;height:1200px;overflow:hidden;background:var(--canvas)}
body{position:relative;font-family:'Lato',sans-serif;color:var(--text)}
.slide{position:absolute;width:454px;height:255px;background:var(--paper);box-shadow:0 0 4px rgba(0,0,0,.18);overflow:hidden}
.abs{position:absolute}
.slide-title{position:absolute;left:16px;top:14px;font-family:'Montserrat',sans-serif;font-weight:700;font-size:18.5px;color:var(--navy);letter-spacing:.2px;padding-left:11px;line-height:1.1;white-space:nowrap}
.slide-title::before{content:"";position:absolute;left:0;top:2px;width:2px;height:17px;background:var(--orange)}
.lead{font-size:8px;line-height:13px;color:var(--text)}
.footer-rule{position:absolute;left:10px;right:0;bottom:7px;height:0;border-top:1px solid var(--navy)}
.page-num{position:absolute;right:30px;bottom:9px;font-size:4.5px;color:var(--orange);font-family:'Montserrat',sans-serif}
.footer-mark{position:absolute;right:10px;bottom:10px;width:13px;height:13px;border-radius:50%;background:var(--navy)}
.wordmark{font-family:'Montserrat',sans-serif;font-weight:700;color:var(--navy);display:flex;align-items:center;gap:9px;white-space:nowrap}
.wordmark .dot{width:30px;height:30px;border-radius:50%;background:var(--navy);flex:none}
.cover-title{font-family:'Montserrat',sans-serif;font-weight:800;color:var(--navy);font-size:19px;white-space:nowrap}
.tagline{color:var(--orange);font-size:14px;white-space:nowrap}
.agenda-item{position:absolute;width:95px}
.agenda-item .num{font-family:'Montserrat',sans-serif;font-weight:700;color:var(--orange);font-size:16px;padding-bottom:4px;border-bottom:1px solid var(--rule)}
.agenda-item h3{font-family:'Montserrat',sans-serif;font-weight:600;color:var(--navy);font-size:9.5px;margin:6px 0 5px}
.agenda-item p{font-size:5px;line-height:8.5px;color:var(--text)}
.legend{position:absolute;width:110px}
.legend h4{font-family:'Lato',sans-serif;font-weight:700;color:var(--orange);font-size:8px;display:flex;align-items:center;gap:6px;white-space:nowrap}
.legend p{font-size:5px;line-height:8px;color:var(--text);margin-top:4px}
.legend.left{text-align:right}
.legend.left h4{justify-content:flex-end}
.legend.left p{padding-right:13px}
.legend.right p{padding-left:13px}
.swatch{width:7px;height:7px;border-radius:50%;display:inline-block;flex:none}
.media{position:absolute;border-radius:5px}
.step{position:absolute;width:122px;text-align:center}
.step h4{font-family:'Montserrat',sans-serif;font-weight:700;color:var(--orange);font-size:8px;margin-top:8px}
.step p{font-size:7.5px;line-height:9px;color:var(--text);margin-top:3px}
.card{position:absolute;top:100px;width:99px;height:115px;border:1px solid var(--rule);border-radius:4px;background:#fff;padding:0 10px}
.card .icon{margin-top:15px;width:26px;height:26px;background:#eef0f3;border-radius:2px;display:flex;align-items:center;justify-content:center}
.card h4{margin-top:17px;font-size:7px;font-weight:700;color:var(--navy);border-left:1px solid var(--orange);padding-left:4px;white-space:nowrap}
.card p{margin-top:9px;font-size:5.5px;line-height:9px;color:var(--muted)}
.card.featured{background:var(--orange);border-color:var(--orange)}
.card.featured .icon{background:#fff}
.card.featured h4{color:#fff;border-left-color:#fff}
.card.featured p{color:#fbe3d4}
.contact{position:absolute;display:flex;align-items:center;gap:9px}
.contact .badge{width:24px;height:24px;border-radius:50%;background:var(--navy);display:flex;align-items:center;justify-content:center}
.contact b{display:block;font-size:7px;color:var(--orange);font-weight:700}
.contact span{font-size:7px;color:var(--text)}
</style>
</head>
<body>

<section class="slide" style="left:41px;top:41px">
  <div class="wordmark abs" style="left:21px;top:39px;font-size:15px"><span class="dot"></span>VELMORA QUILL INDUSTRIES</div>
  <h1 class="cover-title abs" style="left:17px;top:112px">VELMORA QUILL INDUSTRIES</h1>
  <p class="tagline abs" style="left:17px;top:145px">Engineering AI Transformations</p>
  <p class="lead abs" style="left:17px;top:175px;width:265px;line-height:12px">Lorem ipsum dolor sit amet, consectetur adipiscing elit, sed do eiusmod tempor incididunt ut labore et dolore magna aliqua. Quis ipsum suspendisse ultrices gravida. Risus commodo viverra maecenas accumsan lacus vel facilisis.</p>
  <div class="footer-rule"></div><span class="page-num">01</span><span class="footer-mark"></span>
</section>

<section class="slide" style="left:555px;top:41px">
  <h2 class="slide-title">AI TRANSFORMATION ROADMAP</h2>
  <p class="lead abs" style="left:14px;top:48px;width:340px">Lorem ipsum dolor sit amet, consectetur adipiscing elit, sed do eiusmod tempor incididunt ut labore et dolore magna aliqua. Quis ipsum suspendisse ultrices gravida. Risus commodo viverra maecenas accumsan lacus vel facilisis.</p>
  <svg class="abs" style="left:0;top:0" width="454" height="255" viewBox="0 0 454 255" font-family="Lato, sans-serif">
    <path d="M52 165 C85 150 95 160 118 170 C150 180 160 170 185 168 C215 150 230 155 251 168 C280 180 300 175 318 168 C345 148 360 152 385 169" fill="none" stroke="#9aa0a8" stroke-width=".8" stroke-dasharray="3 2"/>
    <g stroke="#163a6e" stroke-width="1.2" fill="#fff">
      <line x1="52" y1="136" x2="52" y2="165"/><line x1="184" y1="136" x2="184" y2="168"/><line x1="318" y1="136" x2="318" y2="168"/>
      <circle cx="52" cy="123" r="13"/><circle cx="184" cy="123" r="13"/><circle cx="318" cy="123" r="13"/>
    </g>
    <g fill="#163a6e"><circle cx="52" cy="165" r="3.5"/><circle cx="184" cy="168" r="3.5"/><circle cx="318" cy="168" r="3.5"/></g>
    <g stroke="#d65f1f" stroke-width="1.2" fill="#fff">
      <line x1="118" y1="170" x2="118" y2="199"/><line x1="251" y1="168" x2="251" y2="199"/><line x1="385" y1="169" x2="385" y2="199"/>
      <circle cx="118" cy="212" r="13"/><circle cx="251" cy="212" r="13"/><circle cx="385" cy="212" r="13"/>
    </g>
    <g fill="#d65f1f"><circle cx="118" cy="170" r="3.5"/><circle cx="251" cy="168" r="3.5"/><circle cx="385" cy="169" r="3.5"/></g>
    <g font-size="8" text-anchor="middle" fill="#163a6e"><text x="52" y="126">01</text><text x="184" y="126">03</text><text x="318" y="126">05</text></g>
    <g font-size="8" text-anchor="middle" fill="#d65f1f"><text x="118" y="215">02</text><text x="251" y="215">04</text><text x="385" y="215">06</text></g>
    <g font-size="7.5" text-anchor="middle" fill="#d65f1f"><text x="118" y="113">Design</text><text x="251" y="113">Scale</text><text x="385" y="113">Optimize</text></g>
    <g font-size="7.5" text-anchor="middle" fill="#163a6e"><text x="52" y="191">Discover</text><text x="184" y="191">Pilot</text><text x="318" y="191">Integrate</text></g>
    <g font-size="5" text-anchor="middle" fill="#3a3f47">
      <text x="118" y="123">Excepteur sint occaecat</text><text x="118" y="130">cupidatat non proident, est</text><text x="118" y="137">laborum.</text>
      <text x="251" y="123">Excepteur sint occaecat</text><text x="251" y="130">cupidatat non proident,</text><text x="251" y="137">est laborum.</text>
      <text x="385" y="123">Excepteur sint occaecat</text><text x="385" y="130">cupidatat non proident,</text><text x="385" y="137">est laborum.</text>
      <text x="52" y="201">Excepteur sint occaecat</text><text x="52" y="208">cupidatat non proident,</text><text x="52" y="215">est laborum.</text>
      <text x="184" y="201">Excepteur sint occaecat</text><text x="184" y="208">cupidatat non proident, est</text><text x="184" y="215">laborum.</text>
      <text x="318" y="201">Excepteur sint occaecat</text><text x="318" y="208">cupidatat non proident,</text><text x="318" y="215">est laborum.</text>
    </g>
  </svg>
  <div class="footer-rule"></div><span class="page-num">05</span><span class="footer-mark"></span>
</section>

<section class="slide" style="left:41px;top:328px">
  <h2 class="slide-title" style="top:15px">AGENDA</h2>
  <div class="agenda-item" style="left:186px;top:32px"><div class="num">01</div><h3>Introduction</h3><p>Lorem ipsum dolor sit amet, consectetur adipiscing elit, sed do eiusmod tempor incididunt magna aliqua.</p></div>
  <div class="agenda-item" style="left:319px;top:32px"><div class="num">02</div><h3>About Us</h3><p>Lorem ipsum dolor sit amet, consectetur adipiscing elit, sed do eiusmod tempor incididunt magna aliqua.</p></div>
  <div class="agenda-item" style="left:50px;top:124px"><div class="num">03</div><h3>Our Services</h3><p>Lorem ipsum dolor sit amet, consectetur adipiscing elit, sed do eiusmod tempor incididunt magna aliqua.</p></div>
  <div class="agenda-item" style="left:185px;top:124px"><div class="num">04</div><h3>Roadmap</h3><p>Lorem ipsum dolor sit amet, consectetur adipiscing elit, sed do eiusmod tempor incididunt magna aliqua.</p></div>
  <div class="agenda-item" style="left:319px;top:124px"><div class="num">05</div><h3>How We Work</h3><p>Lorem ipsum dolor sit amet, consectetur adipiscing elit, sed do eiusmod tempor incididunt magna aliqua.</p></div>
  <div class="footer-rule"></div><span class="page-num">02</span><span class="footer-mark"></span>
</section>

<section class="slide" style="left:555px;top:328px">
  <h2 class="slide-title" style="top:15px">DATA-DRIVEN IMPACT</h2>
  <div class="legend left" style="left:36px;top:74px"><h4>Velmora Quill Industries 1 <span class="swatch" style="background:var(--blue-1)"></span></h4><p>Duis aute irure dolor in reprehenderit in voluptate velit esse cillum dolore eu fugiat nulla pariatur.</p></div>
  <div class="legend left" style="left:36px;top:121px"><h4>Velmora Quill Industries 2 <span class="swatch" style="background:var(--blue-2)"></span></h4><p>Duis aute irure dolor in reprehenderit in voluptate velit esse cillum dolore eu fugiat nulla pariatur.</p></div>
  <div class="legend left" style="left:36px;top:168px"><h4>Velmora Quill Industries 3 <span class="swatch" style="background:var(--blue-5)"></span></h4><p>Duis aute irure dolor in reprehenderit in voluptate velit esse cillum dolore eu fugiat nulla pariatur.</p></div>
  <div class="legend right" style="left:307px;top:74px"><h4><span class="swatch" style="background:var(--blue-4)"></span> Velmora Quill Industries 4</h4><p>Duis aute irure dolor in reprehenderit in voluptate velit esse cillum dolore eu fugiat nulla pariatur.</p></div>
  <div class="legend right" style="left:307px;top:121px"><h4><span class="swatch" style="background:var(--navy-deep)"></span> Velmora Quill Industries 5</h4><p>Duis aute irure dolor in reprehenderit in voluptate velit esse cillum dolore eu fugiat nulla pariatur.</p></div>
  <div class="legend right" style="left:307px;top:168px"><h4><span class="swatch" style="background:var(--blue-6)"></span> Velmora Quill Industries 6</h4><p>Duis aute irure dolor in reprehenderit in voluptate velit esse cillum dolore eu fugiat nulla pariatur.</p></div>
  <svg class="abs" style="left:152px;top:79px" width="148" height="124" viewBox="0 0 150 130" role="img" aria-label="Pie chart of six segments">
    <ellipse cx="75" cy="70" rx="72" ry="56" fill="#0b3f7d"/>
    <rect x="3" y="56" width="144" height="14" fill="#0b3f7d"/>
    <g transform="translate(75 56)">
      <path d="M0 0 L17 -51 A72 52 0 0 1 68 12 Z" fill="#1a7fcc"/>
      <path d="M0 0 L68 12 A72 52 0 0 1 -10 52 Z" fill="#1369c0"/>
      <path d="M0 0 L-10 52 A72 52 0 0 1 -58 30 Z" fill="#0c2f5e"/>
      <path d="M0 0 L-58 30 A72 52 0 0 1 -50 -37 Z" fill="#0f5fb8"/>
      <path d="M0 0 L-50 -37 A72 52 0 0 1 17 -51 Z" fill="#6fb1e6"/>
    </g>
  </svg>
  <div class="footer-rule"></div><span class="page-num">06</span><span class="footer-mark"></span>
</section>

<section class="slide" style="left:41px;top:616px">
  <h2 class="slide-title" style="top:14px">ABOUT US</h2>
  <p class="lead abs" style="left:14px;top:54px;width:205px">Lorem ipsum dolor sit amet, consectetur adipiscing elit, sed do eiusmod tempor incididunt ut labore et dolore magna aliqua. Quis ipsum suspendisse ultrices gravida. Risus commodo viverra maecenas accumsan lacus vel facilisis.</p>
  <p class="lead abs" style="left:14px;top:129px;width:205px">Lorem ipsum dolor sit amet, consectetur adipiscing elit, sed do eiusmod tempor incididunt ut labore et dolore magna aliqua. Quis ipsum suspendisse ultrices gravida. Risus commodo viverra maecenas accumsan lacus vel facilisis.</p>
  <div class="media" style="left:237px;top:12px;width:204px;height:200px;background:radial-gradient(circle at 52% 42%,#6aa7d8 0%,#2c5f8f 30%,#163a5e 65%,#0f2640 100%)" role="img" aria-label="Photo of an open hand holding a glowing AI network hologram"></div>
  <div class="footer-rule"></div><span class="page-num">03</span><span class="footer-mark"></span>
</section>

<section class="slide" style="left:555px;top:616px">
  <h2 class="slide-title" style="top:15px">HOW WE WORK</h2>
  <p class="lead abs" style="left:14px;top:50px;width:300px">Lorem ipsum dolor sit amet, consectetur adipiscing elit, sed do eiusmod tempor incididunt ut labore et dolore magna aliqua.</p>
  <div class="media" style="left:13px;top:91px;width:122px;height:100px;background:radial-gradient(circle at 55% 50%,#3d9ae8 0%,#14467e 45%,#0b1a2c 100%)" role="img" aria-label="Image of glowing blue data cubes"></div>
  <div class="media" style="left:154px;top:91px;width:122px;height:100px;background:linear-gradient(180deg,#0e1f3d 0%,#1c4d8c 50%,#3a7fd0 75%,#182f5a 100%)" role="img" aria-label="Image of a city skyline at night with light trails"></div>
  <div class="media" style="left:295px;top:91px;width:122px;height:100px;background:radial-gradient(circle at 45% 45%,#8a9bb8 0%,#4d5f80 45%,#2a3650 100%)" role="img" aria-label="Image of a hand holding a glowing AI chip"></div>
  <div class="step" style="left:13px;top:191px"><h4>STRATEGY FIRST</h4><p>Align AI with business priorities</p></div>
  <div class="step" style="left:154px;top:191px"><h4>BUILD &amp; SCALE</h4><p>From pilots to enterprise-wide solutions</p></div>
  <div class="step" style="left:295px;top:191px"><h4>DELIVER IMPACT</h4><p>Measurable ROI, continuous optimization</p></div>
  <div class="footer-rule"></div><span class="page-num">07</span><span class="footer-mark"></span>
</section>

<section class="slide" style="left:41px;top:903px">
  <h2 class="slide-title" style="top:16px">OUR SERVICES</h2>
  <p class="lead abs" style="left:14px;top:53px;width:340px">Lorem ipsum dolor sit amet, consectetur adipiscing elit, sed do eiusmod tempor incididunt ut labore et dolore magna aliqua. Quis ipsum suspendisse ultrices gravida. Risus commodo viverra maecenas accumsan lacus vel facilisis.</p>
  <div class="card" style="left:13px"><div class="icon"><svg width="16" height="16" viewBox="0 0 16 16" fill="none" stroke="#d65f1f" stroke-width="1"><circle cx="8" cy="7" r="4.5"/><line x1="6" y1="13" x2="10" y2="13"/><line x1="6.5" y1="15" x2="9.5" y2="15"/></svg></div><h4>Intelligent Automation</h4><p>Excepteur sint occaecat cupidatat non proident, sunt mollit anim id est laborum.</p></div>
  <div class="card" style="left:123px"><div class="icon"><svg width="16" height="16" viewBox="0 0 16 16" fill="none" stroke="#d65f1f" stroke-width="1"><rect x="2" y="3" width="12" height="11"/><line x1="5" y1="12" x2="5" y2="9"/><line x1="8" y1="12" x2="8" y2="7"/><line x1="11" y1="12" x2="11" y2="5"/></svg></div><h4>Decision Intelligence</h4><p>Excepteur sint occaecat cupidatat non proident, sunt mollit anim id est laborum.</p></div>
  <div class="card featured" style="left:232px"><div class="icon"><svg width="16" height="16" viewBox="0 0 16 16" fill="none" stroke="#163a6e" stroke-width="1"><rect x="4" y="4" width="8" height="8"/><path d="M6 2v2M10 2v2M6 12v2M10 12v2M2 6h2M2 10h2M12 6h2M12 10h2"/></svg></div><h4>Data &amp; AI Enablement</h4><p>Excepteur sint occaecat sunt in culpa qui deserunt mollit anim id est laborum.</p></div>
  <div class="card" style="left:342px"><div class="icon"><svg width="16" height="16" viewBox="0 0 16 16" fill="none" stroke="#d65f1f" stroke-width="1"><circle cx="5" cy="5" r="2"/><circle cx="11" cy="5" r="2"/><path d="M2 13c0-3 6-3 6 0M8 13c0-3 6-3 6 0"/></svg></div><h4>AI Implementation</h4><p>Excepteur sint occaecat cupidatat non proident, sunt mollit anim id est laborum.</p></div>
  <div class="footer-rule"></div><span class="page-num">04</span><span class="footer-mark"></span>
</section>

<section class="slide" style="left:555px;top:903px">
  <div class="wordmark abs" style="left:21px;top:42px;font-size:15px"><span class="dot"></span>VELMORA QUILL INDUSTRIES</div>
  <h1 class="cover-title abs" style="left:17px;top:113px;font-size:20px">THANK YOU</h1>
  <p class="tagline abs" style="left:17px;top:150px">Engineering AI Transformations</p>
  <div class="contact" style="left:15px;top:183px"><span class="badge"><svg width="12" height="12" viewBox="0 0 24 24" fill="#fff"><path d="M6.6 10.8a15 15 0 0 0 6.6 6.6l2.2-2.2a1 1 0 0 1 1-.25 11.4 11.4 0 0 0 3.6.57 1 1 0 0 1 1 1V20a1 1 0 0 1-1 1A17 17 0 0 1 3 4a1 1 0 0 1 1-1h3.5a1 1 0 0 1 1 1c0 1.25.2 2.45.57 3.6a1 1 0 0 1-.25 1z"/></svg></span><div><b>CALL US</b><span>+ 1 555 014 2290</span></div></div>
  <div class="contact" style="left:121px;top:183px"><span class="badge"><svg width="12" height="12" viewBox="0 0 24 24" fill="none" stroke="#fff" stroke-width="2"><rect x="3" y="5" width="18" height="14"/><path d="M3 6l9 7 9-7"/></svg></span><div><b>EMAIL</b><span>info@velmoraquill.com</span></div></div>
  <div class="footer-rule"></div><span class="page-num">08</span><span class="footer-mark"></span>
</section>

</body>
</html>
```